Corvane Capital Business Cards

These are professional business cards that are for my family office.
Put fake emails and phone numbers as of now until I finalize those components. This family office controls my families investments, assets, and future. The cards should be professional.
..
.
.
.
I just uploaded another variation of a logo I would like to see as a business card to I am inbeteen which logo to use

Target Market(s)

business

Industry/Entity Type

business

Contact Information for Business Card

Professional, wealth related, finance related.

Requirements
Must have
• Logo

```html
<!DOCTYPE html>
<html lang="en">
<head>
<meta charset="utf-8">
<title>Corvane Capital Business Cards</title>
<link href="https://fonts.googleapis.com/css2?family=Cinzel:wght@400;600;700&family=Arimo:wght@400&display=swap" rel="stylesheet">
<style>
  :root {
    --backdrop: #3d3d3d;
    --navy: #1b1f2d;
    --paper: #ffffff;
    --silver: #a9a9ab;
    --ink: #1e2230;
    --muted: #8a8a8e;
    --rule: #d6d6d8;
  }
  html, body {
    margin: 0;
    width: 1200px;
    height: 803px;
    overflow: hidden;
    background: var(--backdrop);
  }
  .canvas {
    position: relative;
    width: 1200px;
    height: 803px;
  }
  .card {
    position: absolute;
    top: 250px;
    width: 520px;
    height: 300px;
    border-radius: 22px;
    overflow: hidden;
    box-shadow: 0 14px 30px rgba(0,0,0,0.35);
  }
  .card--front { left: 60px; background: var(--paper); }
  .card--back { left: 620px; background: var(--navy); }

  /* Front: brand block */
  .brand {
    position: absolute;
    left: 30px;
    top: 48px;
    width: 210px;
    text-align: center;
  }
  .brand__mark {
    display: block;
    margin: 0 auto 14px;
    width: 78px;
    height: 78px;
    border: 2px solid var(--ink);
    border-radius: 50%;
    box-sizing: border-box;
  }
  .brand__name {
    font-family: 'Cinzel', serif;
    font-weight: 600;
    font-size: 19px;
    color: var(--ink);
    letter-spacing: 0.5px;
    margin: 0;
  }
  .divider {
    position: absolute;
    left: 255px;
    top: 40px;
    width: 1px;
    height: 150px;
    background: linear-gradient(to bottom, rgba(0,0,0,0), var(--rule) 30%, var(--rule) 70%, rgba(0,0,0,0));
  }

  /* Front: contact block */
  .contact {
    position: absolute;
    left: 282px;
    top: 40px;
    font-family: 'Arimo', sans-serif;
    color: #55575c;
  }
  .contact__name {
    font-family: 'Cinzel', serif;
    font-weight: 700;
    font-size: 20px;
    color: var(--ink);
    margin: 0;
    letter-spacing: 0.5px;
  }
  .contact__role {
    font-size: 11px;
    color: var(--muted);
    margin: 0 0 14px;
  }
  .contact__address {
    font-size: 12px;
    line-height: 16px;
    margin: 0 0 10px;
  }
  .contact__list {
    list-style: none;
    margin: 0;
    padding: 0;
    font-size: 12px;
    line-height: 16px;
  }
  .contact__list li {
    display: flex;
    align-items: center;
    gap: 8px;
  }
  .contact__list svg { width: 10px; height: 10px; flex: none; }

  /* Front: bottom bands */
  .band-navy {
    position: absolute;
    left: 0;
    top: 232px;
    width: 440px;
    height: 26px;
    background: var(--navy);
  }
  .band-navy__url {
    position: absolute;
    left: 78px;
    top: 6px;
    font-family: 'Arimo', sans-serif;
    font-size: 12px;
    letter-spacing: 3px;
    color: var(--paper);
  }
  .band-silver {
    position: absolute;
    left: 440px;
    top: 222px;
    width: 80px;
    height: 36px;
    background: var(--silver);
  }
  .seal {
    position: absolute;
    left: 424px;
    top: 224px;
    width: 40px;
    height: 40px;
    border-radius: 50%;
    background: var(--paper);
    border: 2px solid var(--navy);
    box-sizing: border-box;
  }

  /* Back */
  .back-brand {
    position: absolute;
    inset: 0;
    display: flex;
    flex-direction: column;
    align-items: center;
    justify-content: center;
  }
  .back-brand__mark {
    width: 110px;
    height: 110px;
    border: 2px solid var(--paper);
    border-radius: 50%;
    box-sizing: border-box;
    margin-bottom: 22px;
  }
  .back-brand__name {
    font-family: 'Cinzel', serif;
    font-weight: 600;
    font-size: 26px;
    color: var(--paper);
    letter-spacing: 1px;
    margin: 0;
  }
</style>
</head>
<body>
<main class="canvas">
  <section class="card card--front" aria-label="Business card front">
    <div class="brand">
      <span class="brand__mark"></span>
      <p class="brand__name">Corvane Capital</p>
    </div>
    <div class="divider"></div>
    <div class="contact">
      <h1 class="contact__name">Elliot Marsh</h1>
      <p class="contact__role">President</p>
      <p class="contact__address">4210 Alder Court<br>Lakeview, Canada 20418</p>
      <ul class="contact__list">
        <li>
          <svg viewBox="0 0 10 10"><path d="M2 0.5 L3.6 2.6 L2.7 3.6 Q4 6 6.4 7.3 L7.4 6.4 L9.5 8 L8.3 9.5 Q4.5 9.3 2 6.5 Q0.2 4 0.5 1.7 Z" fill="var(--ink)"/></svg>
          555-201-4830
        </li>
        <li>
          <svg viewBox="0 0 10 10"><rect x="2" y="0.5" width="6" height="9" rx="1" fill="none" stroke="var(--ink)" stroke-width="1"/><circle cx="5" cy="8" r="0.6" fill="var(--ink)"/></svg>
          555-201-7762
        </li>
        <li>
          <svg viewBox="0 0 10 10"><rect x="0.5" y="2" width="9" height="6.5" fill="var(--ink)"/><path d="M0.5 2 L5 5.8 L9.5 2" fill="none" stroke="#fff" stroke-width="0.9"/></svg>
          info@corvanecapital.com
        </li>
      </ul>
    </div>
    <div class="band-navy"><span class="band-navy__url">www.corvanecapital.com</span></div>
    <div class="band-silver"></div>
    <span class="seal"></span>
  </section>

  <section class="card card--back" aria-label="Business card back">
    <div class="back-brand">
      <span class="back-brand__mark"></span>
      <p class="back-brand__name">Corvane Capital</p>
    </div>
  </section>
</main>
</body>
</html>
```